design a construction company business card

Design business card around our logo. Card must have all the typical info: name, title, address, phone, email, business name, etc. Somewhere on the card I would like to see our motto "Built on integrity... Inspired by commitment." Consider adding a splash of bright orange to the card to complement the blues and silvers/grays in the logo. We are open to metallic inks, textures, etc. We would like to see options on both light and dark backgrounds. The font in the logo is Euro Technic Extended Regular.

```html
<!DOCTYPE html>
<html lang="en">
<head>
<meta charset="utf-8">
<title>Harlow Contracting – Business Card</title>
<link rel="stylesheet" href="https://fonts.googleapis.com/css2?family=Lato:wght@400;700&family=Roboto+Condensed:wght@400&display=swap">
<style>
  :root {
    --backdrop: #666666;
    --card-dark: #1f1f1f;
    --brand-blue: #2f7fd6;
    --blue-top: #1a73c1;
    --blue-bottom: #2a4196;
    --ink-light: #f2f2f2;
    --rule: #5a5a5a;
  }
  * { margin: 0; padding: 0; box-sizing: border-box; }
  html, body {
    width: 1200px; height: 900px; overflow: hidden;
    background: var(--backdrop);
    font-family: "Lato", sans-serif;
  }
  .canvas { position: relative; width: 1200px; height: 900px; }

  .card {
    position: absolute;
    top: 275px;
    height: 296px;
    box-shadow: 3px 4px 6px rgba(0,0,0,0.35);
  }
  .card--front {
    left: 120px; width: 480px;
    background: var(--card-dark);
    border-radius: 0 48px 0 48px;
  }
  .card--back {
    left: 620px; width: 477px;
    background: linear-gradient(180deg, var(--blue-top), var(--blue-bottom));
    border-radius: 48px 0 48px 0;
  }

  .wordmark {
    position: absolute;
    text-align: center;
    font-family: "Lato", sans-serif;
    font-weight: 700;
    letter-spacing: 0.04em;
    line-height: 1.1;
  }
  .card--front .wordmark {
    left: 30px; width: 190px; top: 124px;
    color: var(--brand-blue);
  }
  .card--front .wordmark__name { font-size: 34px; display: block; }
  .card--front .wordmark__sub { font-size: 11px; display: block; margin-top: 4px; letter-spacing: 0.06em; }

  .card--back .wordmark {
    left: 0; width: 100%; top: 118px;
    color: #ffffff;
  }
  .card--back .wordmark__name { font-size: 62px; display: block; }
  .card--back .wordmark__sub { font-size: 17px; display: block; margin-top: 6px; letter-spacing: 0.06em; }

  .divider {
    position: absolute;
    left: 238px; top: 83px;
    width: 1px; height: 127px;
    background: var(--rule);
  }

  .contact {
    position: absolute;
    left: 265px; top: 80px;
    color: var(--ink-light);
    text-transform: uppercase;
  }
  .contact__name {
    color: var(--brand-blue);
    font-weight: 700;
    font-size: 16px;
    letter-spacing: 0.02em;
    line-height: 20px;
  }
  .contact__title { font-size: 12px; line-height: 14px; margin-bottom: 7px; }
  .contact__row {
    display: flex; align-items: center; gap: 4px;
    font-size: 12.5px; line-height: 18.5px;
  }
  .contact__row svg { width: 11px; height: 11px; fill: var(--brand-blue); flex: none; }
  .contact__address { font-size: 12.5px; line-height: 16px; margin-top: 7px; }

  .motto {
    position: absolute;
    left: 0; width: 100%; top: 222px;
    text-align: center;
    color: #ffffff;
    font-family: "Roboto Condensed", sans-serif;
    font-size: 13px;
    letter-spacing: 0.02em;
    text-transform: uppercase;
  }
</style>
</head>
<body>
<main class="canvas">

  <section class="card card--front" aria-label="Business card front">
    <div class="wordmark">
      <span class="wordmark__name">HARLOW</span>
      <span class="wordmark__sub">CONTRACTING, INC.</span>
    </div>

    <div class="divider"></div>

    <div class="contact">
      <p class="contact__name">Jonathan Smith</p>
      <p class="contact__title">Managing Director</p>
      <p class="contact__row">
        <svg viewBox="0 0 24 24" aria-hidden="true"><path d="M6.6 10.8a15.1 15.1 0 0 0 6.6 6.6l2.2-2.2a1 1 0 0 1 1-.25 11.4 11.4 0 0 0 3.6.6 1 1 0 0 1 1 1V20a1 1 0 0 1-1 1A17 17 0 0 1 3 4a1 1 0 0 1 1-1h3.5a1 1 0 0 1 1 1c0 1.25.2 2.45.6 3.6a1 1 0 0 1-.25 1z"/></svg>
        <span>044-123 456 789</span>
      </p>
      <p class="contact__row">
        <svg viewBox="0 0 24 24" aria-hidden="true"><path d="M2 5h20v14H2zm2 2v.4l8 5 8-5V7l-8 5z"/></svg>
        <span>info@webname.com</span>
      </p>
      <p class="contact__row">
        <svg viewBox="0 0 24 24" aria-hidden="true"><circle cx="12" cy="12" r="10"/></svg>
        <span>www.websitename.com</span>
      </p>
      <p class="contact__address">421, Address Line Here<br>Country Name, 45452</p>
    </div>
  </section>

  <section class="card card--back" aria-label="Business card back">
    <div class="wordmark">
      <span class="wordmark__name">HARLOW</span>
      <span class="wordmark__sub">CONTRACTING, INC.</span>
    </div>
    <p class="motto">Built on integrity... Inspired by commitment</p>
  </section>

</main>
</body>
</html>
```